VENTURE CAPITAL GROUP BUSINESS CARD DESIGN

Venture Capital Group based in SF looking for a bold business card design. No trendy colour explosion, 3D effects etc. Just "simple" optical effects. Works on your brain, keeps your eye focused and sticks to your mind.
Target Market(s)
Technology startups
Industry/Entity Type
Venture Capital
Contact Information for Business Card
DESMOND WHITLAKE
MANAGING PARTNER
187 FENWORTH ST SAN FRANCISCO, CA 94187
415.555.0142 O
415.555.0147 F
415.555.0193 C
desmond@veldtmoorcapital.ventures

```html
<!DOCTYPE html>
<html lang="en">
<head>
<meta charset="utf-8">
<title>Veldtmoor Capital Group – Business Card</title>
<link href="https://fonts.googleapis.com/css2?family=Cinzel:wght@600&family=Open+Sans:ital,wght@0,400;0,600;1,400&display=swap" rel="stylesheet">
<style>
  :root {
    --green-deep: #0b6b2c;
    --green: #149a3f;
    --green-light: #3cb35e;
    --grey-text: #6d6f71;
    --grey-stripe: #c9cbcc;
    --white: #ffffff;
    --backdrop: #e9ebe9;
  }
  * { margin: 0; padding: 0; box-sizing: border-box; }
  html, body { width: 1200px; height: 872px; overflow: hidden; }
  body {
    background: var(--backdrop);
    font-family: "Open Sans", Arial, sans-serif;
    display: flex;
    align-items: center;
    justify-content: center;
    gap: 60px;
  }
  .card {
    position: relative;
    width: 520px;
    height: 297px;
    overflow: hidden;
    box-shadow: 0 6px 18px rgba(0,0,0,0.18);
  }

  /* Front */
  .card-front { background: var(--white); }
  .brand {
    position: absolute;
    top: 62px;
    left: 0;
    right: 0;
    display: flex;
    align-items: center;
    justify-content: center;
    gap: 14px;
  }
  .brand-dot {
    width: 54px; height: 54px; border-radius: 50%;
    background: var(--green);
  }
  .brand-name {
    font-family: "Cinzel", Georgia, serif;
    font-weight: 600;
    font-size: 24px;
    color: var(--green-deep);
    letter-spacing: 1px;
  }
  .person {
    position: absolute;
    top: 138px; left: 0; right: 0;
    text-align: center;
    color: var(--grey-text);
  }
  .person-name { font-size: 14px; font-weight: 600; letter-spacing: 1.5px; }
  .person-title { font-size: 12px; font-style: italic; margin-top: 2px; }

  .stripe {
    position: absolute; left: 0; right: 0; bottom: 74px;
    height: 7px; background: var(--grey-stripe);
  }
  .band {
    position: absolute; left: 0; right: 0; bottom: 0;
    height: 74px;
    background: linear-gradient(90deg, var(--green-deep), var(--green) 55%, var(--green-deep));
    color: var(--white);
    font-size: 10px;
    line-height: 1.45;
    display: flex;
    justify-content: space-between;
    align-items: center;
    padding: 0 22px;
  }
  .band-right { text-align: right; }

  /* Back */
  .card-back {
    background: linear-gradient(90deg, var(--green-deep) 0%, var(--green) 22%, var(--green-light) 50%, var(--green) 78%, var(--green-deep) 100%);
  }
  .back-contact {
    position: absolute; top: 26px; left: 0; right: 0;
    text-align: center; color: var(--white);
    font-size: 11px; line-height: 1.5;
  }
  .back-mark {
    position: absolute; top: 96px; left: 50%;
    transform: translateX(-50%);
    width: 120px; height: 120px; border-radius: 50%;
    background: rgba(255,255,255,0.85);
  }
  .back-name {
    position: absolute; bottom: 36px; left: 0; right: 0;
    text-align: center;
    font-family: "Cinzel", Georgia, serif;
    font-weight: 600; font-size: 20px;
    color: var(--white); letter-spacing: 1px;
  }
</style>
</head>
<body>
  <section class="card card-front" aria-label="Business card front">
    <div class="brand">
      <span class="brand-dot"></span>
      <span class="brand-name">Veldtmoor Capital Group</span>
    </div>
    <div class="person">
      <p class="person-name">DESMOND WHITLAKE</p>
      <p class="person-title">Managing Partner</p>
    </div>
    <div class="stripe"></div>
    <div class="band">
      <div class="band-left">
        <p>187 FENWORTH ST · San Francisco, CA 94187</p>
        <p>415.555.0142 O</p>
        <p>415.555.0147 F</p>
        <p>415.555.0193 C</p>
      </div>
      <div class="band-right">
        <p>desmond@veldtmoorcapital.ventures</p>
        <p>www.veldtmoorcapital.com</p>
      </div>
    </div>
  </section>

  <section class="card card-back" aria-label="Business card back">
    <div class="back-contact">
      <p>desmond@veldtmoorcapital.ventures</p>
      <p>www.veldtmoorcapital.com</p>
    </div>
    <div class="back-mark"></div>
    <p class="back-name">Veldtmoor Capital Group</p>
  </section>
</body>
</html>
```